OrchardLane Kiosk Signage

OrchardLane sell fresh fruit and vegetables online and from road side Kiosks.

We need to adapt the current logo for use as signs that will be displayed on roadside kiosks, please see the attached images to view and understand what the Kiosks look like.
The sign needs to:

1. Capture the attention of drivers and
2. Invite them to stop and purchase fresh fruit and veg
3. Communicate the URL www.OrchardLaneProduce.example.nz
4. Communicate the OrchardLane brand
5. Use current logos and imagery

Solution

The designs must closely reflect the current OrchardLane logo (see files attached) and need to include the website. www.OrchardLaneProduce.example.nz The colour palleted also needs to closely resemble the website.

The designs will be used for laser printed signage on vinyl for two applications

1. Kiosk front width: 2.400m x height: 1.000m (94 inches x 40 inches)
2. Kiosk sides: width 0.400m x height: 1.000m (15 inches x 40 inches)

The region where the kiosk's will display is large open space, green hills and fresh fruit and veg growers (orchards and farms everywhere). The region is well known for horticulture, agriculture, viticulture and farming.

The Kiosk images are attached (P1340537, P1350158, P1350159)
OrchardLane logo (round tree)
OrchardLane logo
Updates

Please note, the OrchardLane kiosk signage brief has been updated. (sorry for the inconvenience, but I think we uploaded an unfinished brief) 

We look forward to your submissions. 

Cheers, OrchardLane 

Target Market(s)

Passers buy - mainly in cars as the signage will be displayed on road side fruit and veg stalls. So the signage will be viewed by the general public, and capture those that are interested in purchasing fresh fruit and veg (direct from the farm or orchard)

Industry/Entity Type

Agriculture

Requirements
Must have
• Must match current logo and reflect the design aspects of the website www.orchardlaneproduce.example.nz
Needs to clearly communicate whats for sale, value and fresh produce
Nice to have
• It would be nice to make the tree component of the logo a feature.

```html
<!DOCTYPE html>
<html lang="en">
<head>
<meta charset="utf-8">
<title>OrchardLane Kiosk Side Sign</title>
<link rel="stylesheet" href="https://fonts.googleapis.com/css2?family=Tinos:wght@700&family=Archivo+Black&display=swap">
<style>
  :root {
    --night: #050505;
    --cream: #f4efe2;
    --navy: #1d3d63;
    --red: #d9141d;
    --wine: #760d12;
    --white: #ffffff;
  }
  * { margin: 0; padding: 0; box-sizing: border-box; }
  html, body { width: 1200px; height: 3195px; overflow: hidden; background: var(--white); }
  .sign { position: relative; width: 1200px; height: 3195px; overflow: hidden; background: var(--white); }

  .brand-band {
    position: absolute; left: 0; top: 0; width: 1200px; height: 605px;
    background: var(--night);
    display: flex; align-items: center; justify-content: center; gap: 50px;
  }
  .brand-name {
    font-family: "Tinos", serif; font-weight: 700; font-size: 150px;
    color: var(--cream); line-height: 1;
  }
  .brand-dot { width: 170px; height: 170px; border-radius: 50%; background: var(--cream); flex: none; }

  .headline { position: absolute; left: 0; width: 1200px; text-align: center; font-family: "Tinos", serif; font-weight: 700; line-height: 1; }
  .headline-kind { top: 650px; font-size: 100px; color: var(--navy); }
  .headline-today { top: 835px; font-size: 190px; color: var(--navy); }
  .headline-price { top: 1075px; font-size: 180px; color: var(--red); }

  .produce-photo {
    position: absolute; left: 0; top: 1250px; width: 1200px; height: 1945px;
    background: linear-gradient(180deg, #ffffff 0%, #4f7a2c 6%, #7ea64a 28%, #3f6e28 52%, #a8c46a 60%, #f2a12a 70%, #c8241e 80%, #f2c53a 90%, #7a1f3a 100%);
  }

  .call {
    position: absolute; left: 0; width: 1200px; text-align: center;
    font-family: "Archivo Black", sans-serif; line-height: 1;
    text-shadow: 0 0 6px var(--white), 4px 4px 0 var(--white), -4px -4px 0 var(--white), 4px -4px 0 var(--white), -4px 4px 0 var(--white);
  }
  .call-come { top: 1420px; font-size: 250px; color: var(--wine); }
  .call-buy { top: 1725px; font-size: 250px; color: var(--red); }
  .web-address {
    position: absolute; left: 0; top: 1990px; width: 1200px; text-align: center;
    font-family: "Archivo Black", sans-serif; font-size: 52px; color: var(--white);
    text-shadow: 3px 3px 0 var(--night), -2px -2px 0 var(--night), 2px -2px 0 var(--night), -2px 2px 0 var(--night);
  }
</style>
</head>
<body>
<main class="sign">
  <header class="brand-band">
    <span class="brand-name">OrchardLane</span>
    <span class="brand-dot"></span>
  </header>

  <p class="headline headline-kind">Fruit &amp; Vegetable</p>
  <p class="headline headline-today">TODAY’s</p>
  <p class="headline headline-price">BEST PRICE</p>

  <div class="produce-photo" role="img" aria-label="Fresh produce: broccoli, cauliflower, asparagus, lettuce, avocado, orange, red apple, bananas and grapes"></div>

  <p class="call call-come">COME</p>
  <p class="call call-buy">&amp; BUY!</p>
  <p class="web-address">www.orchardlaneproduce.example.nz</p>
</main>
</body>
</html>
```